Qvx Brightforge Website

All the descriptions are available in the attached file. The designer has to structure the website and find the right images and icons. The website should look modern and avoid using images of real humans rather use animated images. Please note that the design should include home page, all the 4 services page , the contact us would be at the bottom of home page.

```html
<!DOCTYPE html>
<html lang="en">
<head>
<meta charset="utf-8">
<title>Qvx Brightforge</title>
<link href="https://fonts.googleapis.com/css2?family=Lato:wght@400;700&display=swap" rel="stylesheet">
<style>
:root{
  --blue:#0a6fe0;
  --ink:#111;
  --body:#333;
  --muted:#555;
  --pale:#f1f6fc;
  --wave:#d6e6f8;
  --field:#eeeeee;
  --gold:#f2b53a;
  --footer:#1e1e1e;
  --art-a:#c9d4f5;
  --art-b:#e9eefb;
}
*{margin:0;padding:0;box-sizing:border-box}
html,body{width:1200px;height:3489px;overflow:hidden;background:#fff}
body{font-family:'Lato',sans-serif;color:var(--body)}
.page{position:relative;width:1200px;height:3489px;overflow:hidden}
.abs{position:absolute}
.brand{font-weight:700;color:var(--blue);display:flex;align-items:center;gap:10px}
.brand .dot{width:16px;height:16px;background:var(--blue);border-radius:50%}
.nav a{position:absolute;top:32px;font-size:17.5px;color:var(--ink);text-decoration:none}
.btn{position:absolute;display:flex;align-items:center;justify-content:center;background:var(--blue);color:#fff;font-weight:700;font-size:17px;border-radius:22px}
.art{position:absolute;background:linear-gradient(135deg,var(--art-b),var(--art-a))}
h1.hero{position:absolute;left:117px;top:224px;font-size:32px;line-height:38.5px;color:var(--ink);font-weight:700;width:420px}
h2.sec{position:absolute;font-size:35px;font-weight:700;color:var(--ink)}
h3.svc{position:absolute;font-size:23px;font-weight:700;color:var(--ink)}
p.copy{position:absolute;font-size:13px;line-height:25.7px;color:var(--muted)}
.icon-disc{position:absolute;border-radius:50%;background:#fff;box-shadow:0 4px 14px rgba(10,111,224,.12);display:flex;align-items:center;justify-content:center}
.field{position:absolute;background:var(--field);border-radius:6px;font-size:13px;color:#666;padding:14px 16px}
.footer h4{position:absolute;top:3210px;font-size:23px;color:#fff;font-weight:700}
.footer ul{position:absolute;top:3255px;list-style:none}
.footer li{font-size:13px;color:#fff;line-height:25.7px}
.footer .contact li{display:flex;align-items:flex-start;gap:6px;line-height:31px}
</style>
</head>
<body>
<div class="page">

  <header>
    <div class="brand abs" style="left:119px;top:46px;font-size:30px"><span class="dot"></span>Qvx Brightforge</div>
    <nav class="nav">
      <a style="left:565px">Home</a>
      <a style="left:657px">Services <svg width="12" height="8" viewBox="0 0 12 8"><path d="M1 1l5 5 5-5" fill="none" stroke="#111" stroke-width="1.5"/></svg></a>
      <a style="left:770px">Products</a>
      <a style="left:896px">Blog</a>
      <a style="left:980px">Contact us</a>
    </nav>
  </header>

  <section class="hero-section">
    <h1 class="hero">Empower your digital<br>journey with our advanced<br>IT solutions. From data to<br>web and mobile apps, we've<br>got you covered.</h1>
    <div class="btn" style="left:115px;top:459px;width:137px;height:41px">Contact Us</div>
    <div class="art" role="img" aria-label="Illustration of a team collaborating at desks with charts and laptops" style="left:515px;top:196px;width:663px;height:373px;border-radius:12px;background:linear-gradient(135deg,#eef0fc,#cdd0f5)"></div>
  </section>

  <svg class="abs" style="left:0;top:630px" width="1200" height="130" viewBox="0 0 1200 130">
    <path d="M0 62 C220 -10 420 20 600 70 C800 125 1000 110 1200 60" fill="none" stroke="var(--wave)" stroke-width="7"/>
  </svg>

  <section class="about">
    <div class="abs" style="left:120px;top:733px;width:456px;height:456px;border-radius:50%;border:5px solid var(--wave)"></div>
    <div class="abs" role="img" aria-label="Isometric illustration of a digital workspace with dashboards and people" style="left:128px;top:741px;width:440px;height:440px;border-radius:50%;background:radial-gradient(circle,#c9cde6,#8e93bd)"></div>
    <h2 class="sec" style="left:626px;top:782px">About Us</h2>
    <p class="copy" style="left:623px;top:833px;width:450px">We are a forward-thinking IT consulting firm specializing in providing cutting-edge data analytics, web application development, and mobile app development services. Our passion for innovation and technology drives us to deliver tailor-made solutions that empower businesses to thrive in the digital landscape.We take pride in our ability to collaborate with early-stage startups as their technology partner, helping them navigate the challenges of launching and scaling heir ventures. Our team of experienced professionals works closely with clients, understanding their unique requirements and goals, to craft bespoke solutions that</p>
    <div class="btn" style="left:623px;top:1090px;width:138px;height:41px">Read More</div>
  </section>

  <section class="services">
    <svg class="abs" style="left:0;top:1230px" width="1200" height="1470" viewBox="0 0 1200 1470" preserveAspectRatio="none">
      <path d="M0 40 C250 0 420 70 650 60 C880 50 1000 10 1200 30 L1200 1440 C1000 1470 700 1420 400 1450 C200 1470 100 1460 0 1450 Z" fill="var(--pale)"/>
    </svg>
    <h2 class="sec" style="left:0;width:1212px;text-align:center;top:1333px">Services</h2>

    <h3 class="svc" style="left:116px;top:1440px">Data Analytics</h3>
    <p class="copy" style="left:116px;top:1488px;width:440px">At Qvx Brightforge, our proficiency consists of linking your leadership team's objectives with the relevant data that holds significance. We recognize the importance of not only delivering precise and dependable data but also presenting it in a format that is easily comprehensible and aligned with your business goals.</p>
    <div class="btn" style="left:115px;top:1636px;width:137px;height:41px">Learn More</div>
    <div class="art" role="img" aria-label="Illustration of analysts presenting data dashboards" style="left:663px;top:1433px;width:407px;height:235px;background:linear-gradient(135deg,#f6f9fc,#cfe0ea)"></div>
    <div class="icon-disc" style="left:599px;top:1582px;width:104px;height:104px">
      <svg width="64" height="52" viewBox="0 0 64 52"><g fill="var(--blue)"><rect x="4" y="32" width="8" height="20"/><rect x="18" y="24" width="8" height="28"/><rect x="32" y="30" width="8" height="22"/><rect x="46" y="16" width="8" height="36"/></g><path d="M6 24 L22 12 L36 20 L54 4" fill="none" stroke="var(--blue)" stroke-width="3"/></svg>
    </div>

    <div class="art" role="img" aria-label="Illustration of developers building a website layout" style="left:116px;top:1741px;width:403px;height:236px;background:linear-gradient(135deg,#f7f7fa,#e6e6ee)"></div>
    <div class="icon-disc" style="left:476px;top:1890px;width:104px;height:104px">
      <svg width="56" height="50" viewBox="0 0 56 50"><rect x="2" y="2" width="52" height="46" rx="6" fill="var(--blue)"/><rect x="2" y="12" width="52" height="2" fill="#fff"/><path d="M20 24l-7 7 7 7M36 24l7 7-7 7M31 22l-6 18" fill="none" stroke="#fff" stroke-width="3"/></svg>
    </div>
    <h3 class="svc" style="left:608px;top:1750px">Web Development</h3>
    <p class="copy" style="left:605px;top:1796px;width:440px">At Qvx Brightforge, we are a trailblazing web development company committed to delivering cutting-edge digital solutions that empower businesses to excel in the ever-evolving online landscape. Our team of seasoned professionals combines technical prowess with a passion for innovation,</p>
    <div class="btn" style="left:604px;top:1944px;width:137px;height:41px">Learn More</div>

    <h3 class="svc" style="left:116px;top:2052px">Mobile App Dovelopment</h3>
    <p class="copy" style="left:116px;top:2099px;width:440px">At Qvx Brightforge, we are a pioneering mobile app development company dedicated to crafting exceptional digital experiences that captivate and engage users across various platforms. Our team of expert developers and designers combines passion, innovation, and technical mastery to transform your ideas into intuitive, user-friendly mobile apps that</p>
    <div class="btn" style="left:115px;top:2249px;width:137px;height:41px">Learn More</div>
    <div class="art" role="img" aria-label="Illustration of a large smartphone with charts and people using apps" style="left:663px;top:2047px;width:407px;height:239px;background:linear-gradient(135deg,#eef6fc,#cfe6f6)"></div>
    <div class="icon-disc" style="left:622px;top:2192px;width:104px;height:104px">
      <svg width="44" height="52" viewBox="0 0 44 52"><rect x="4" y="2" width="26" height="46" rx="4" fill="none" stroke="var(--blue)" stroke-width="3"/><circle cx="32" cy="36" r="9" fill="var(--blue)"/><circle cx="32" cy="36" r="3" fill="#fff"/></svg>
    </div>

    <div class="art" role="img" aria-label="Illustration of a startup team meeting with a mentor" style="left:116px;top:2372px;width:403px;height:236px;background:linear-gradient(135deg,#ffffff,#e8eef8)"></div>
    <div class="icon-disc" style="left:476px;top:2521px;width:104px;height:104px">
      <svg width="52" height="52" viewBox="0 0 52 52"><path d="M48 4C34 4 22 12 16 26l10 10c14-6 22-18 22-32z" fill="var(--blue)"/><circle cx="34" cy="18" r="5" fill="#fff"/><path d="M16 26l-10 2 6-10 10-2zM26 36l-2 10 10-6 2-10z" fill="var(--blue)"/><path d="M6 46l8-8M4 38l6-6M14 48l6-6" stroke="var(--blue)" stroke-width="3"/></svg>
    </div>
    <h3 class="svc" style="left:603px;top:2379px">Start-Up Tech Partner</h3>
    <p class="copy" style="left:605px;top:2424px;width:440px">At Qvx Brightforge, we are committed to supporting early-stage start-ups on their journey to success by providing comprehensive technical partner services. Our team of industry veterans collaborates with entrepreneurs to refine their ideas, develop minimum viable products (MVPs)&nbsp; strategize market entry and execute effective</p>
    <div class="btn" style="left:604px;top:2574px;width:137px;height:41px">Learn More</div>
  </section>

  <section class="contact">
    <h2 class="sec" style="left:0;width:1206px;text-align:center;top:2748px">Contact Us</h2>
    <div class="field" style="left:194px;top:2811px;width:399px;height:43px">First Name</div>
    <div class="field" style="left:617px;top:2811px;width:400px;height:43px">Last Name</div>
    <div class="field" style="left:194px;top:2865px;width:399px;height:43px">Email Address</div>
    <div class="field" style="left:617px;top:2865px;width:400px;height:43px">Contact Number</div>
    <div class="field" style="left:194px;top:2921px;width:823px;height:104px">Message</div>
    <div class="btn" style="left:536px;top:3063px;width:137px;height:43px;background:var(--gold)">Submit</div>
  </section>

  <footer class="footer">
    <svg class="abs" style="left:0;top:3120px" width="1200" height="369" viewBox="0 0 1200 369" preserveAspectRatio="none">
      <path d="M0 52 C300 20 450 40 650 50 C850 60 1000 40 1200 16 L1200 369 L0 369Z" fill="var(--footer)"/>
      <path d="M0 32 C300 0 450 26 650 36 C850 46 1000 26 1200 4" fill="none" stroke="var(--wave)" stroke-width="7"/>
    </svg>
    <div class="brand abs" style="left:116px;top:3220px;font-size:24px"><span class="dot"></span>Qvx Brightforge</div>
    <p class="abs" style="left:117px;top:3310px;width:200px;font-size:13px;line-height:25.7px;color:#fff">We are a forward-thinking IT consulting firm specializing in providing cutting-edge</p>
    <div class="btn" style="left:115px;top:3401px;width:159px;height:41px">Get Started Now</div>

    <h4 style="left:382px">Quick Links</h4>
    <ul style="left:384px"><li>Home</li><li>Services</li><li>Products</li><li>Blog</li><li>Contact us</li></ul>

    <h4 style="left:608px">Other Links</h4>
    <ul style="left:610px"><li>Terms And Conditions</li><li>Privacy Policy</li><li>Careers</li></ul>

    <h4 style="left:860px">Other Links</h4>
    <ul class="contact" style="left:862px;top:3250px">
      <li><svg width="14" height="12" viewBox="0 0 14 12" style="margin-top:10px"><rect x="0" y="1" width="14" height="10" fill="#fff"/><path d="M0 1l7 6 7-6" fill="none" stroke="#1e1e1e" stroke-width="1.3"/></svg>hello@qvxbrightforge.example</li>
      <li><svg width="14" height="14" viewBox="0 0 24 24" style="margin-top:8px"><path fill="#fff" d="M6.6 10.8a15 15 0 006.6 6.6l2.2-2.2c.3-.3.7-.4 1-.2 1.1.4 2.3.6 3.6.6.6 0 1 .4 1 1V20c0 .6-.4 1-1 1A17 17 0 013 4c0-.6.4-1 1-1h3.5c.6 0 1 .4 1 1 0 1.3.2 2.5.6 3.6.1.3 0 .7-.2 1z"/></svg>+61 (08) 5550 2714</li>
      <li><svg width="14" height="16" viewBox="0 0 24 28" style="margin-top:8px"><path fill="#fff" d="M12 0a9 9 0 00-9 9c0 7 9 19 9 19s9-12 9-19a9 9 0 00-9-9zm0 13a4 4 0 110-8 4 4 0 010 8z"/></svg>Suite 12/48 Harbourline Road,<br>Eastmere WA 6199</li>
    </ul>

    <p class="abs" style="left:0;width:1272px;text-align:center;top:3458px;font-size:13px;color:#fff">© 2023 Qvx Brightforge&nbsp; All rights reserved</p>
  </footer>

</div>
</body>
</html>
```